Tuition Center Website

We need a new web site for a tutoring company based in sydney.

We only teach senior highschool students and pride ourselves on building the students abilities to think their way through life.

I would like a bright and vibrant website that looks professional and modern.
It needs to look simple and neat but also have the functionality we need.
Images and flash would be good.

Please keep in mind that the site must be appealing to a younger audience.

We need a multipage website with the following navigation bars:

1.Home (As logo not "home" button)
I would like a news box/ticker somewhere that can stream our chatterbook and pipstream feeds and also any news updates we want to put up.
Subscribe to newsletter button.

2. About us.
This needs to be a pull down into:
-What we do
-Why we do it
-How we do it

3. Courses
Pulldown into:
-Maths
-English
-Science
(we may need to attach extra pages behind these e.g. Courses/Science/Physics or Courses/Science/Chemistry and possibly add a link to a new zandlo form)

4. Inspired
This page is like a blog page where we can upload videos, links to articles that we find to be inspiring and hopefully will inspire others.

5. Inspire
This is a recruitment page. Only content here.

6. Contact us.
Mapquill map widget and a 'contact us' form

* Our branding requires green close to #12FF3D

***Please have a look at the current website.
@ www.velmorlearning.com.au

Thanks everybody hope the revision of my brief is better and more informative than my last one

Target Market(s)

senior highschool students aged 15-19, parents ( to a lesser degree)

Industry/Entity Type

It Company

Requirements
Must have
• Ability to change content on pages.

The green doesn't have to be everywhere, but it must be obvious that it is our colour.

Nice to have
• Sites with a nicer mix of images and flash will be given more consideration. But then again, if you amaze us, you amaze us and we will go with your design.
Should not have
• Should stay away from ocre, brown colours and serif fonts.

```html
<!DOCTYPE html>
<html lang="en">
<head>
<meta charset="utf-8">
<title>Contact Us – Velmor Learning</title>
<link href="https://fonts.googleapis.com/css2?family=Open+Sans:wght@300;400;600;700&display=swap" rel="stylesheet">
<style>
:root{
  --brand:#8ce000;
  --brand-dark:#6fb800;
  --brand-deep:#4f8d1a;
  --ink:#1a1a1a;
  --text:#333;
  --muted:#999;
  --line:#e4e4e4;
  --field:#f7f7f7;
  --field-border:#cfcfcf;
  --footer:#3a3a3a;
  --white:#fff;
}
*{box-sizing:border-box;margin:0;padding:0}
html,body{width:1164px;height:1200px;overflow:hidden;background:var(--white);font-family:'Open Sans',Arial,sans-serif;color:var(--text)}
.page{position:relative;width:1164px;height:1200px}
.abs{position:absolute}

/* header */
.brand{left:117px;top:14px;display:flex;align-items:center;gap:12px}
.brand-mark{width:74px;height:74px;background:var(--brand)}
.brand-name{font-size:22px;font-weight:600;color:var(--ink);line-height:1.1}
.consult{left:873px;top:26px;display:flex;gap:8px;align-items:flex-start}
.consult-text{font-size:17px;font-weight:300;color:#3a4a66;line-height:20px;letter-spacing:-.5px;white-space:nowrap}
.phone{left:876px;top:68px;font-size:28px;font-weight:400;color:var(--ink);letter-spacing:-.3px}

/* nav */
.nav{left:0;top:129px;width:1164px;height:52px;background:linear-gradient(#9ae81a,#7ccc00);border-top:2px solid #ddd}
.nav-item{top:13px;font-size:14px;font-weight:600;color:#2e4a0a;padding:4px 8px;white-space:nowrap;text-shadow:0 1px 0 rgba(255,255,255,.3)}
.nav-item.is-active{background:var(--white);border-radius:4px;color:var(--ink);border:1px solid #cfe7a4}
.follow{right:116px;top:0;height:50px;display:flex;align-items:center;gap:9px;font-size:12px;font-weight:600;color:#4a6a14;white-space:nowrap}
.follow-link{color:var(--white)}

/* hero */
.hero{left:0;top:181px;width:1164px;height:331px;background:linear-gradient(90deg,#e9ebeb 0%,#f8f8f6 30%,#d6d8d4 55%,#cfd1cd 100%)}
.hero-photo{left:720px;top:181px;width:300px;height:331px;background:radial-gradient(ellipse at 50% 40%,#c9a28a 0%,#5a3a2e 55%,#2a1e1a 100%);opacity:.85}
.hero-title{left:117px;top:318px;font-size:50px;font-weight:300;color:var(--ink);letter-spacing:-1.5px;white-space:nowrap}

/* band */
.band{left:0;top:514px;width:1164px;height:97px;background:var(--brand)}
.band-text{left:117px;top:531px;width:950px;font-size:21.5px;font-weight:700;color:#1a2a05;line-height:32px;letter-spacing:-.6px}

/* content */
.section-title{left:117px;top:642px;font-size:25px;font-weight:600;color:var(--ink)}
.section-rule{left:282px;top:659px;width:766px;height:5px;background:#f0f0f0}
.lead{left:118px;top:694px;font-size:16px;font-weight:400;color:#444}
.label{left:117px;font-size:14px;color:var(--ink);white-space:nowrap}
.field{left:236px;width:319px;height:30px;background:var(--field);border:1px solid var(--field-border);border-radius:2px;font-size:11px;font-style:italic;color:var(--muted);padding:7px 9px}
.field-select{display:flex;justify-content:space-between;padding-right:0}
.select-btn{width:25px;height:28px;margin-top:-7px;background:#3d3d3d;display:flex;align-items:center;justify-content:center}
.comments{left:118px;top:961px;width:437px;height:90px}
.submit{left:118px;top:1066px;width:95px;height:35px;background:linear-gradient(#7fc235,var(--brand-deep));border-radius:3px;color:var(--white);font-size:19px;text-align:center;line-height:35px}
.map{left:657px;top:755px;width:391px;height:294px;border:2px solid #d2d2d2;background:linear-gradient(135deg,#e6e8dc,#d8dfc6 45%,#efe9c9 70%,#e3e1d4)}

/* footer */
.footer{left:0;top:1140px;width:1164px;height:60px;background:var(--footer);border-top:3px solid #2a2a2a}
.copyright{left:117px;top:1161px;font-size:13px;color:var(--white)}
.footer-links{right:116px;top:1161px;display:flex;gap:14px;font-size:13px;color:var(--white);white-space:nowrap}
</style>
</head>
<body>
<div class="page">

  <header>
    <div class="abs brand">
      <div class="brand-mark"></div>
      <div class="brand-name">Velmor<br>Learning</div>
    </div>
    <div class="abs consult">
      <svg width="36" height="38" viewBox="0 0 36 38" aria-hidden="true">
        <path d="M5 22 V17 A13 13 0 0 1 31 17 V22" fill="none" stroke="#333" stroke-width="3"/>
        <rect x="2" y="18" width="7" height="11" rx="2" fill="#333"/>
        <rect x="27" y="18" width="7" height="11" rx="2" fill="#333"/>
        <path d="M30 29 Q28 35 18 35" fill="none" stroke="#333" stroke-width="2"/>
      </svg>
      <div class="consult-text">Call for a<br>free Consultation !</div>
    </div>
    <div class="abs phone">555-014-2870</div>
  </header>

  <nav class="abs nav">
    <span class="abs nav-item" style="left:124px">Home</span>
    <span class="abs nav-item" style="left:220px">About Us</span>
    <span class="abs nav-item" style="left:338px">Courses</span>
    <span class="abs nav-item" style="left:449px">Inspired</span>
    <span class="abs nav-item" style="left:561px">Inspire</span>
    <span class="abs nav-item is-active" style="left:664px;top:14px">Contact Us</span>
    <div class="abs follow">Follow Us <span class="follow-link">netweave</span><span class="follow-link">chatterbook</span><span class="follow-link">pipstream</span></div>
  </nav>

  <section>
    <div class="abs hero" role="img" aria-label="Soft blurred office background"></div>
    <div class="abs hero-photo" role="img" aria-label="Photo of a smiling support agent wearing a headset"></div>
    <h1 class="abs hero-title">CONTACT US</h1>
  </section>

  <div class="abs band"></div>
  <p class="abs band-text">Want to book in a free trial lesson or have questions about our Year 10 or HSC tutoring classes? Use the form below to get in touch with us.</p>

  <main>
    <h2 class="abs section-title">Get in Touch</h2>
    <div class="abs section-rule"></div>
    <p class="abs lead">Leave us a message and we will be in touch shortly!</p>

    <span class="abs label" style="top:762px">First Name :</span>
    <div class="abs field" style="top:755px">Enter Your first Name...</div>
    <span class="abs label" style="top:816px">Last Name :</span>
    <div class="abs field" style="top:809px">Enter Your Last Name...</div>
    <span class="abs label" style="top:870px">Email address :</span>
    <div class="abs field" style="top:863px">Enter Your Email address...</div>
    <span class="abs label" style="top:924px">Type of Enquiry :</span>
    <div class="abs field field-select" style="top:918px">Select type of enquiry...
      <span class="select-btn"><svg width="8" height="5" viewBox="0 0 8 5"><path d="M0 0h8L4 5z" fill="#fff"/></svg></span>
    </div>
    <div class="abs field comments">Enter Comments...</div>
    <div class="abs submit">Submit</div>

    <div class="abs map" role="img" aria-label="Mapquill map widget showing the office location"></div>
  </main>

  <footer>
    <div class="abs footer"></div>
    <span class="abs copyright">© Velmor Learning. All rights reserved.</span>
    <div class="abs footer-links"><span>Home</span><span>About Us</span><span>Courses</span><span>Inspired</span><span>Inspire</span><span>Contact Us</span></div>
  </footer>

</div>
</body>
</html>
```